SkyvornQ Business Cards and Stationary Design

Need a design for our business cards and stationary. I want to carry on the theme of the logo. I want the business cards to have a design on the back. I would like the business cards and the stationary to carry the same theme, design scheme, and branding

Target Market(s)

Airlines and Maintenance Facilities

Industry/Entity Type

Aviation

Contact Information for Business Card

Name
Position Title
Address: 4827 Trellis Hollow Road, Fort Pierce, Florida, 34951
Office Number
Mobile Number
Email
Website

Font styles to use
Serif
Sans Serif

Colors

Designer to choose colors to be used in the design.

```html
<!DOCTYPE html>
<html lang="en">
<head>
<meta charset="utf-8">
<title>SkyvornQ Business Card</title>
<link href="https://fonts.googleapis.com/css2?family=Roboto:wght@400;500;700&display=swap" rel="stylesheet">
<style>
  :root {
    --backdrop: #2a2a2a;
    --paper: #f2f2f2;
    --navy: #06244a;
    --navy-deep: #0a2a6a;
    --blue-mid: #0a4fb0;
    --blue-glow: #13a6ee;
    --white: #ffffff;
  }
  * { margin: 0; padding: 0; box-sizing: border-box; }
  html, body { width: 1200px; height: 960px; overflow: hidden; }
  body { background: var(--backdrop); font-family: "Roboto", Arial, sans-serif; position: relative; }

  .card { position: absolute; width: 600px; height: 343px; border-radius: 20px; overflow: hidden; }
  .card-front { left: 314px; top: 113px; background: var(--paper); }
  .card-back { left: 311px; top: 472px; background: var(--navy); }

  .front-panel { position: absolute; left: 0; top: 0; width: 600px; height: 343px; }

  .brand { position: absolute; left: 0; width: 336px; display: flex; flex-direction: column; align-items: center; }
  .brand-front { top: 112px; }
  .brand-mark { border-radius: 50%; }
  .brand-front .brand-mark { width: 78px; height: 78px; border: 7px solid var(--blue-mid); }
  .brand-name { font-weight: 700; letter-spacing: 4px; text-transform: uppercase; }
  .brand-front .brand-name { color: var(--navy); font-size: 28px; margin-top: 14px; padding-left: 4px; }

  .contact { position: absolute; left: 376px; top: 66px; color: var(--white); }
  .contact-name { font-size: 21px; font-weight: 700; text-transform: uppercase; line-height: 24px; }
  .contact-title { font-size: 14px; font-weight: 500; text-transform: uppercase; line-height: 16px; }
  .contact-address { margin-top: 45px; font-size: 14px; line-height: 19px; }
  .contact-list { list-style: none; margin-top: 9px; font-size: 14px; line-height: 19px; }
  .contact-list li { display: flex; align-items: center; gap: 8px; }
  .contact-list svg { width: 14px; height: 14px; fill: var(--white); flex: none; }

  .brand-back { top: 76px; width: 600px; height: 176px; }
  .brand-back .brand-mark { width: 176px; height: 176px; border: 12px solid var(--white); }
  .brand-back .brand-name {
    position: absolute; left: 0; top: 88px; width: 600px;
    transform: translateY(-50%);
    text-align: center; color: var(--white);
    font-size: 18px; letter-spacing: 3px; padding-left: 3px; line-height: 22px;
  }
  .back-web { position: absolute; left: 0; width: 600px; top: 290px; text-align: center; color: var(--white); font-size: 14px; letter-spacing: 5.5px; padding-left: 5.5px; }
</style>
</head>
<body>
  <section class="card card-front">
    <svg class="front-panel" viewBox="0 0 600 343" aria-hidden="true">
      <defs>
        <radialGradient id="panelGlow" cx="510" cy="150" r="240" gradientUnits="userSpaceOnUse">
          <stop offset="0" stop-color="var(--blue-glow)"/>
          <stop offset="0.55" stop-color="var(--blue-mid)"/>
          <stop offset="1" stop-color="var(--navy-deep)"/>
        </radialGradient>
      </defs>
      <path d="M336 0 H600 V343 H336 V95 L354 78 L336 60 Z" fill="var(--navy)"/>
      <path d="M341 0 H600 V343 H341 V97 L359 78 L341 58 Z" fill="var(--white)"/>
      <path d="M343 0 H600 V343 H343 V98 L361 78 L343 57 Z" fill="url(#panelGlow)"/>
    </svg>

    <div class="brand brand-front">
      <span class="brand-mark"></span>
      <span class="brand-name">SkyvornQ</span>
    </div>

    <div class="contact">
      <p class="contact-name">Dalia Renwick</p>
      <p class="contact-title">CEO/Founder</p>
      <p class="contact-address">4827 Trellis Hollow Road<br>Fort Pierce, Florida, 34951</p>
      <ul class="contact-list">
        <li><svg viewBox="0 0 16 16"><path d="M3.6 1.2 6 3.8 4.7 5.6c.8 1.9 2.3 3.5 4.3 4.4l1.6-1.3 2.6 2.4-1.4 2.6C6.6 13.8 1.9 8.6 1.3 2.9z"/></svg>772 510 4386</li>
        <li><svg viewBox="0 0 16 16"><path d="M4 1h8v14H4zm1.5 1.5v9h5v-9zM7.2 12.5h1.6v1.3H7.2z" fill-rule="evenodd"/></svg>772 903 1658</li>
        <li><svg viewBox="0 0 16 16"><path d="M1 4h14v9H1zm1 .5 6 4.5 6-4.5z"/></svg>info@skyvornq.com</li>
        <li><svg viewBox="0 0 16 16"><circle cx="8" cy="8" r="6.5"/></svg>www.skyvornq.com</li>
      </ul>
    </div>
  </section>

  <section class="card card-back">
    <div class="brand brand-back">
      <span class="brand-mark"></span>
      <span class="brand-name">SkyvornQ</span>
    </div>
    <p class="back-web">www.skyvornq.com</p>
  </section>
</body>
</html>
```